International Clinical Software Company needs a new business card design

We are looking for a new business card design for our company that has recently expanded into the UK market, making us a multinational company.
After having rebranded our website and produced a new style guide, we are looking for a business card that is creative and attention grabbing, while being consistent with the style and colour scheme used on the new website, www.plumvora.example
We produce care management technology for the aged care market, but the main aspect we aim to communicate is the human element of our software, and the way it assists in providing better care for aged people, and stronger relationships between aged people and the staff that care for them.
Our current business card is a dark green with gold text, which makes the text quite difficult to read, not very aesthetically appealing and the colour scheme looks quite dated.
We would like something fresh and modern, that can still be colourful but doesn't use large blocks of dark colour, and uses the colours within our logo.
Something tying in with the leaves that are used in our logo could work quite nicely, along with the Autumn/Fall colours of soft greens, yellows and reds (also in our existing logo). However also happy to look at fresh, completely out of the box ideas we may not have yet considered.
Target Market(s)
The people that receive this business card work in the aged card or health industry and are either corporate/management level staff or clinical (Registered Nurses, care workers etc.)
Industry/Entity Type
Health Product
Contact Information for Business Card
Company Name - BrindlewayCare
Company locations: United Kingdom, Australia, New Zealand
Staff Details:
Staff name: Derek Mallow
Staff job title: Executive Chairman
Staff email: d.mallow@plumvora.example
Office phone number: 01742 918576
Font styles to use
Other font styles liked:
- Calibri
Requirements
Must have
- Must include the BrindlewayCare brand name in it's current font
- Must include logo (3 leaves in gold circle)
- Must include Business Card Details
Nice to have
- Elements of gold
- White space
- Something autumn themed but not too cliched
Should not have
- No blue - used by a major competitor and we would like to differentiate from them
- Large blocks of dark green colour (the green that appears in our leaves on the logo on our current business card is the background colour and it is far too dark)

```html
<!DOCTYPE html>
<html lang="en">
<head>
<meta charset="utf-8">
<title>BrindlewayCare – Business Card</title>
<link rel="stylesheet" href="https://fonts.googleapis.com/css2?family=Open+Sans:wght@300;400;600&display=swap">
<style>
  :root {
    --backdrop: #ece8e1;
    --card: #ffffff;
    --gold: #b3a584;
    --gold-soft: #c9bd9f;
    --crimson: #a8163f;
    --leaf-sage: #e4e6d2;
    --leaf-straw: #ece5c8;
    --leaf-rose: #efd3d3;
    --shadow: rgba(60, 45, 25, 0.18);
  }
  html, body {
    margin: 0;
    padding: 0;
    width: 1200px;
    height: 780px;
    overflow: hidden;
    background: var(--backdrop);
    font-family: "Open Sans", "Calibri", sans-serif;
  }
  .card {
    position: absolute;
    left: 80px;
    top: 90px;
    width: 1040px;
    height: 600px;
    background: var(--card);
    box-shadow: 0 14px 40px var(--shadow);
    overflow: hidden;
  }
  .leaf-art {
    position: absolute;
    left: 600px;
    top: -60px;
    width: 420px;
    height: 520px;
  }
  .brand {
    position: absolute;
    left: 60px;
    top: 140px;
    display: flex;
    align-items: center;
    gap: 28px;
  }
  .brand-dot {
    width: 190px;
    height: 190px;
    border: 8px solid var(--gold);
    border-radius: 50%;
    box-sizing: border-box;
  }
  .brand-name {
    font-weight: 300;
    font-size: 82px;
    color: var(--gold);
    letter-spacing: -1px;
    line-height: 1;
  }
  .person {
    position: absolute;
    left: 72px;
    top: 352px;
  }
  .person-name {
    margin: 0;
    font-weight: 600;
    font-size: 38px;
    line-height: 1.1;
    color: var(--gold);
  }
  .person-title {
    margin: 2px 0 0;
    font-weight: 400;
    font-size: 24px;
    color: var(--crimson);
  }
  .divider {
    position: absolute;
    left: 470px;
    right: 0;
    top: 404px;
    height: 2px;
    background: var(--crimson);
  }
  .contact {
    position: absolute;
    left: 72px;
    top: 452px;
    margin: 0;
    padding: 0;
    list-style: none;
    font-size: 23px;
    line-height: 33px;
  }
  .contact-label { color: var(--crimson); }
  .contact-value { color: var(--gold); }
  .website {
    position: absolute;
    right: 60px;
    top: 430px;
    font-size: 22px;
    font-weight: 400;
    color: var(--crimson);
  }
</style>
</head>
<body>
  <main class="card">
    <svg class="leaf-art" viewBox="0 0 420 520" role="img" aria-label="Faint illustration of three overlapping autumn leaves in sage, straw and rose tones">
      <defs>
        <linearGradient id="leaf-wash" x1="0" y1="0" x2="1" y2="1">
          <stop offset="0" stop-color="var(--leaf-sage)"/>
          <stop offset="0.5" stop-color="var(--leaf-straw)"/>
          <stop offset="1" stop-color="var(--leaf-rose)"/>
        </linearGradient>
      </defs>
      <rect x="0" y="0" width="420" height="520" rx="210" fill="url(#leaf-wash)" opacity="0.7"/>
    </svg>

    <div class="brand">
      <div class="brand-dot"></div>
      <span class="brand-name">BrindlewayCare</span>
    </div>

    <div class="person">
      <h1 class="person-name">Derek Mallow</h1>
      <p class="person-title">Executive Chairman</p>
    </div>

    <div class="divider"></div>

    <ul class="contact">
      <li><span class="contact-label">Australia - </span><span class="contact-value">1800 555 019</span></li>
      <li><span class="contact-label">UK - </span><span class="contact-value">01742 918576</span></li>
      <li><span class="contact-label">International calls - </span><span class="contact-value">+61 08 5550 1287</span></li>
      <li><span class="contact-label">E: </span><span class="contact-value">d.mallow@plumvora.example</span></li>
    </ul>

    <span class="website">www.plumvora.example</span>
  </main>
</body>
</html>
```